KRT Flyer to attract applicants 11x17

Lantern Stagehand Collective provides crew for local concerts, filming, theater, and corporate events.
The flyer will be posted on bulletin boards at colleges with theater programs.
Our primary venues are historic theaters in downtown LA
Need a 11x17 poster to attract potential applicants/crew
I have attached a poster that one of our staff made that has all if the relevant info - but i know the poster can look much better than that. I have also attached many images and our logo. It is not necessary to use all of the images, or any of them. The two images of the theater interiors are the venues we operate so they would be the first to include. I can send additional info or images upon request. Thank you

Industry/Entity Type

Entertainment

Requirements
Must have
• APPLY@KRTCREW.EXAMPLE

```html
<!DOCTYPE html>
<html lang="en">
<head>
<meta charset="utf-8">
<title>Lantern Stagehand Collective – Open Positions</title>
<link rel="stylesheet" href="https://fonts.googleapis.com/css2?family=Allura&family=Prata&family=Questrial&display=swap">
<style>
  :root {
    --canvas-bg: #ffffff;
    --night: #120a3e;
    --indigo: #241058;
    --plum: #4a1656;
    --magenta: #b8307a;
    --rose: #e2689e;
    --violet: #7048b8;
    --white: #ffffff;
    --pill-blue: #2a5fb8;
  }
  * { box-sizing: border-box; margin: 0; padding: 0; }
  html, body {
    width: 1200px;
    height: 887px;
    overflow: hidden;
    background: var(--canvas-bg);
  }
  .canvas {
    position: relative;
    width: 1200px;
    height: 887px;
  }
  .poster {
    position: absolute;
    left: 335px;
    top: 34px;
    width: 530px;
    height: 820px;
    overflow: hidden;
    color: var(--white);
    font-family: "Questrial", sans-serif;
    background:
      radial-gradient(ellipse 70% 45% at 100% 62%, rgba(140, 30, 100, 0.55), transparent 70%),
      linear-gradient(180deg, var(--plum) 0%, var(--indigo) 55%, var(--night) 100%);
  }
  .venue-photo {
    position: absolute;
    left: 0;
    top: 0;
    width: 530px;
    height: 340px;
    background:
      radial-gradient(ellipse 16% 9% at 50% 7%, #f6e6f4 0%, rgba(246, 230, 244, 0) 100%),
      radial-gradient(ellipse 30% 34% at 50% 52%, rgba(236, 170, 200, 0.85), transparent 75%),
      radial-gradient(ellipse 22% 30% at 15% 50%, rgba(220, 70, 130, 0.7), transparent 75%),
      radial-gradient(ellipse 22% 30% at 85% 50%, rgba(220, 70, 130, 0.7), transparent 75%),
      linear-gradient(180deg, #7a3c9e 0%, #a2407e 40%, #8a3a8a 70%, rgba(74, 22, 86, 0) 100%);
  }
  .brand {
    position: absolute;
    left: 0;
    width: 100%;
    top: 232px;
    text-align: center;
  }
  .brand-mark {
    display: block;
    margin: 0 auto 10px;
    width: 46px;
    height: 46px;
    border-radius: 50%;
    background: var(--white);
  }
  .brand-name {
    font-size: 15px;
    letter-spacing: 1.5px;
    text-transform: uppercase;
    line-height: 1.3;
    white-space: nowrap;
  }
  .headline {
    position: absolute;
    left: 0;
    width: 100%;
    top: 340px;
    text-align: center;
    font-weight: 400;
  }
  .headline-script {
    display: block;
    font-family: "Allura", cursive;
    font-size: 84px;
    line-height: 70px;
    margin-left: 10px;
  }
  .headline-main {
    display: block;
    font-family: "Prata", serif;
    font-size: 66px;
    line-height: 70px;
    letter-spacing: 0.5px;
    white-space: nowrap;
  }
  .intro {
    position: absolute;
    left: 0;
    width: 100%;
    top: 500px;
    text-align: center;
    font-size: 20px;
    line-height: 26px;
  }
  .gallery {
    position: absolute;
    top: 602px;
    left: 95px;
    display: flex;
    gap: 20px;
  }
  .gallery-photo {
    width: 160px;
    height: 118px;
    border: 2px solid var(--white);
  }
  .gallery-photo.console {
    background: linear-gradient(135deg, #1c1c28 0%, #6e6248 40%, #b09a6a 60%, #3a3024 100%);
  }
  .gallery-photo.lighting {
    background: linear-gradient(135deg, #2a2c80 0%, #8a96e6 35%, #3c3aa0 65%, #1a1a48 100%);
  }
  .apply {
    position: absolute;
    left: 50%;
    top: 744px;
    transform: translateX(-50%);
    height: 28px;
    padding: 0 18px;
    border-radius: 14px;
    background: var(--pill-blue);
    white-space: nowrap;
    font-size: 14px;
    line-height: 28px;
  }
  .website {
    position: absolute;
    left: 0;
    width: 100%;
    top: 784px;
    text-align: center;
    font-size: 17px;
    line-height: 22px;
    letter-spacing: 0.5px;
    white-space: nowrap;
  }
</style>
</head>
<body>
  <div class="canvas">
    <article class="poster">
      <div class="venue-photo" role="img" aria-label="Ornate historic theater interior lit in magenta and violet, with a glowing domed ceiling and carved proscenium"></div>

      <header class="brand">
        <span class="brand-mark" aria-hidden="true"></span>
        <p class="brand-name">Lantern Stagehand Collective</p>
      </header>

      <h1 class="headline">
        <span class="headline-script">Open</span>
        <span class="headline-main">POSITIONS</span>
      </h1>

      <p class="intro">We are Looking for Talented<br>Technicians to add to our Roster<br>of Skilled Professionals</p>

      <div class="gallery">
        <div class="gallery-photo console" role="img" aria-label="Close-up of a digital audio mixing console with glowing screen and faders"></div>
        <div class="gallery-photo lighting" role="img" aria-label="Moving-head stage light hanging from a chained truss with blue beams"></div>
      </div>

      <p class="apply">Send Resume To: APPLY@KRTCREW.EXAMPLE</p>
      <p class="website">www.krtcrew.example</p>
    </article>
  </div>
</body>
</html>
```